Business Card - high end, modern health care

Hey designers!

We need a double sided business card for the boutique, cutting edge physical therapy rehabilitation centre in Sydney's Northern Beaches.

With the most qualified physios in the area The Harbourview Motion Clinic does what other physiotherapy practices do not, we take our time with our patients giving them longer appointments, better physios and therefor faster results!

We guarantee that the service people receive at THMC will be unparalleled.

Hence we need a business card to reflect our modern, boutique, high end service. The final design needs to reflect that we are in a class of our own yet with the feel of beachside retreat.

Below I have attached our logo in both blue on white and white on blue. The exact colour is;
and the font that we have used in our logo is Tex Gyre Aventador.

I like the idea of the blue as the main colour as it is more eye catching and our signage onto the main road will be in this blue and in the interest of consistency across marketing the blue needs to be a part of the design. However I would appreciate a few designs onto a wooden background as this is a visual theme within the fitout of the practice.

The design needs to be of standard size (91x55mm).

Target Market(s)

We target people who have an end outcome in mind and those who have had poor experiences with other providers and ensure that everyone gets the care that they deserve with a premium service that is tailored to the individuals circumstances. As a premium service, the target market is highly educated, business and tech savvy with the additional target market of elderly people who have self funded their retirement and see value in paying for the best ongoing rehabilitation to maintain independence.

Industry/Entity Type

Physical Therapy

Contact Information for Business Card

Name, designation( Titled Musculoskeletal Physiotherapist... there will also be those in the company that have multiple designations ie 5 or 6 words long), phone number, email, facebook, instagram, address

Font styles to use
Sans Serif

Colors

Designer to choose colors to be used in the design.

Requirements
Must have
• Front - The logo as large as possible, blue or wooden theme, and all of the important details.
• Back - A blank space/lines on which to write appointment times (no "Appointment, date, time" etc.)
Nice to have
• facebook url
• logos for facebook and instagram
• Mini logos for the phone and email?

```html
<!DOCTYPE html>
<html lang="en">
<head>
<meta charset="utf-8">
<title>The Harbourview Motion Clinic – Business Card</title>
<link rel="stylesheet" href="https://fonts.googleapis.com/css2?family=Raleway:wght@400;500;600&display=swap">
<style>
  :root {
    --backdrop: #e9e8ee;
    --wood-dark: #3a1810;
    --wood-mid: #6b2e1a;
    --wood-light: #8a4026;
    --card-white: #ffffff;
    --brand-blue: #1558a6;
    --ink: #1b1b1b;
    --rule: #3a3a3a;
    --rule-dashed: #a8a8a8;
    --handle-blue: #2a8fd6;
    --handle-pink: #e45a93;
  }
  * { margin: 0; padding: 0; box-sizing: border-box; }
  html, body { width: 1200px; height: 1000px; overflow: hidden; }
  body {
    background: var(--backdrop);
    font-family: "Raleway", sans-serif;
    color: var(--ink);
    position: relative;
  }
  .card {
    position: absolute;
    width: 658px;
    height: 375px;
    box-shadow: 0 6px 18px rgba(0,0,0,0.25);
    overflow: hidden;
  }
  /* Front */
  .card-front { left: 136px; top: 78px; }
  .wood-surface {
    position: absolute; inset: 0;
    background: linear-gradient(100deg, var(--wood-dark) 0%, var(--wood-mid) 30%, var(--wood-light) 55%, var(--wood-mid) 75%, var(--wood-dark) 100%);
  }
  .front-decor-circle {
    position: absolute;
    left: 283px; top: 5px;
    width: 366px; height: 366px;
    border-radius: 50%;
    background: rgba(255,255,255,0.08);
  }
  .front-brand {
    position: absolute;
    left: 49px; top: 156px;
    display: flex; align-items: center; gap: 10px;
  }
  .brand-dot {
    width: 55px; height: 55px; border-radius: 50%;
    background: var(--card-white);
    flex: none;
  }
  .front-brand-name {
    color: var(--card-white);
    font-weight: 600;
    font-size: 27px;
    line-height: 1.05;
    letter-spacing: 1px;
    text-transform: uppercase;
  }
  /* Back */
  .card-back { left: 437px; top: 548px; background: var(--card-white); height: 376px; }
  .person-name {
    position: absolute; left: 43px; top: 49px;
    font-size: 26px; font-weight: 400;
  }
  .person-name .surname { color: var(--brand-blue); }
  .person-title {
    position: absolute; left: 43px; top: 85px;
    font-size: 15px; font-weight: 500;
  }
  .rule {
    position: absolute; height: 0;
    border-top: 1.5px solid var(--rule);
  }
  .rule-top { left: 43px; top: 119px; width: 370px; }
  .rule-mid { left: 43px; top: 203px; width: 370px; }
  .rule-dashed { left: 47px; top: 285px; width: 570px; border-top: 1.5px dashed var(--rule-dashed); }
  .rule-write { left: 47px; top: 313px; width: 570px; border-top: 1px solid var(--rule); }
  .contact-line {
    position: absolute; left: 43px;
    display: flex; align-items: center; gap: 14px;
    font-size: 17px; font-weight: 500;
  }
  .contact-phone { top: 136px; }
  .contact-email { top: 167px; }
  .contact-line svg { width: 22px; height: 22px; flex: none; }
  .handle-line {
    position: absolute; top: 222px;
    display: flex; align-items: center; gap: 8px;
    font-size: 15px; font-weight: 500;
  }
  .handle-page { left: 43px; }
  .handle-photos { left: 244px; }
  .handle-dot { width: 21px; height: 21px; border-radius: 50%; flex: none; }
  .handle-page .handle-dot { background: var(--handle-blue); }
  .handle-photos .handle-dot { background: var(--handle-pink); }
  .address {
    position: absolute; left: 45px; top: 327px;
    font-size: 15px; font-weight: 500;
  }
  .back-brand {
    position: absolute; left: 452px; top: 88px; width: 156px;
    display: flex; flex-direction: column; align-items: center; gap: 8px;
  }
  .back-brand .brand-dot { width: 100px; height: 100px; background: var(--brand-blue); }
  .back-brand-name {
    color: var(--brand-blue);
    font-weight: 600; font-size: 13px; line-height: 1.25;
    text-align: center; text-transform: uppercase; letter-spacing: 0.5px;
  }
</style>
</head>
<body>
  <section class="card card-front">
    <div class="wood-surface" role="img" aria-label="Dark polished timber grain background"></div>
    <div class="front-decor-circle"></div>
    <div class="front-brand">
      <span class="brand-dot"></span>
      <span class="front-brand-name">The Harbourview<br>Motion Clinic</span>
    </div>
  </section>

  <section class="card card-back">
    <h1 class="person-name">Name of <span class="surname">Person</span></h1>
    <p class="person-title">Musculoskeletal Physiotherapist</p>
    <div class="rule rule-top"></div>

    <div class="contact-line contact-phone">
      <svg viewBox="0 0 24 24" aria-hidden="true">
        <circle cx="12" cy="12" r="10.5" fill="none" stroke="#1b1b1b" stroke-width="1.6"/>
        <path d="M8.6 6.8c.4-.3 1-.3 1.3.1l1.1 1.6c.3.4.2.9-.1 1.2l-.7.6c.5 1.3 1.5 2.4 2.8 3l.6-.7c.3-.4.8-.5 1.2-.2l1.6 1.1c.4.3.5.9.1 1.3l-.8.9c-.6.6-1.5.8-2.3.5-2.8-1.1-4.9-3.2-6-6-.3-.8-.1-1.7.5-2.3z" fill="#1b1b1b"/>
      </svg>
      <span>612.555.0147</span>
    </div>
    <div class="contact-line contact-email">
      <svg viewBox="0 0 24 24" aria-hidden="true">
        <rect x="1" y="5" width="22" height="14" fill="#1b1b1b"/>
        <path d="M1.5 5.5 12 13.5 22.5 5.5" fill="none" stroke="#fff" stroke-width="1.4"/>
        <path d="M1.5 18.5 9 11.5M22.5 18.5 15 11.5" fill="none" stroke="#fff" stroke-width="1.2"/>
      </svg>
      <span>hello@harbourviewmotion.com</span>
    </div>
    <div class="rule rule-mid"></div>

    <div class="handle-line handle-page"><span class="handle-dot"></span><span>page/hvmotion</span></div>
    <div class="handle-line handle-photos"><span class="handle-dot"></span><span>photos_hvmotion</span></div>

    <div class="rule rule-dashed"></div>
    <div class="rule rule-write"></div>
    <p class="address">No.01, Adrs line 01, Adrs line 02, Street, City, Country</p>

    <div class="back-brand">
      <span class="brand-dot"></span>
      <span class="back-brand-name">The Harbourview<br>Motion Clinic</span>
    </div>
  </section>
</body>
</html>
```